BrivoTerna. Lantern of the Steady Harvest. Business card

Professional business card for BrivoTerna (Lantern of the Steady Harvest)
My rationale: Strategy-> Execution-> Results-> Value that lead to the BrivoTerna name: We put the Lantern of the Steady Harvest.
We deliver value to our customers helping them at defining a good strategy (cyan arrow). 90% of well formulated strategies fail due to poor execution so we also consider strategical execution very important (green arrow). Due to the execution we obtain the results (blue arrow). Finally, the results provide feedback to redefine strategy, and the new strategy has to be executed and new results obtained providing new feedback and on and on. It's like a wheel that finally, must create corporate value: value for shareholders, staholders, employees, providers...-

Target Market(s)

CEOs and steering comitees , invewrnent funds

Industry/Entity Type

Business Consultant

Contact Information for Business Card

Teodoro Vinsquel
CEO & Founder
teodoro.vinsquel@brivoterna-example.com
Mobile: +34 655.803.912
www.brivoterna-example.com

Colors

Designer to choose colors to be used in the design.

Requirements
Nice to have
• Nice to hace the words: Strategy, execution, results
• Nice to vave the claim: Lantern of the Steady Harvest
• The three colors should be shown:
• cyan for STRATEGY
• green for EXECUTION
• blue for RESULTS
Should not have
• Complete black background

```html
<!DOCTYPE html>
<html lang="en">
<head>
<meta charset="utf-8">
<title>BrivoTerna – Business Card</title>
<link rel="stylesheet" href="https://fonts.googleapis.com/css2?family=Open+Sans:wght@400;600;700;800&display=swap">
<style>
  :root {
    --bg: #e9e6e3;
    --card: #ffffff;
    --navy: #003399;
    --green: #8cc63f;
    --cyan: #29abe2;
    --ink-light: #ffffff;
  }
  * { box-sizing: border-box; margin: 0; padding: 0; }
  html, body {
    width: 1200px; height: 997px; overflow: hidden;
    background: var(--bg);
    font-family: "Open Sans", Arial, sans-serif;
  }
  .sheet { position: relative; width: 1200px; height: 997px; }
  .card {
    position: absolute; left: 250px; width: 700px; height: 400px;
    background: var(--card);
    box-shadow: 0 4px 14px rgba(0,0,0,0.12);
    overflow: hidden;
  }
  .card--front { top: 68px; }
  .card--back { top: 528px; }

  .front-panels { position: absolute; inset: 0; }

  .brand {
    position: absolute; display: flex; align-items: center; gap: 12px;
    color: var(--navy); font-weight: 800; letter-spacing: -0.5px;
    white-space: nowrap;
  }
  .brand__dot {
    width: 20px; height: 20px; border-radius: 50%; background: var(--cyan); flex: none;
  }
  .card--front .brand { left: 40px; top: 176px; font-size: 36px; }

  .holder {
    position: absolute; right: 34px; top: 30px; text-align: right; color: var(--ink-light);
  }
  .holder__name {
    font-size: 24px; font-weight: 700; padding-bottom: 4px;
    border-bottom: 2px solid var(--ink-light);
  }
  .holder__role { font-size: 14px; margin-top: 4px; }

  .contacts {
    position: absolute; right: 34px; top: 184px; list-style: none;
    color: var(--ink-light); font-size: 13px; text-align: right; line-height: 1.65;
    white-space: nowrap;
  }
  .contacts li { display: flex; justify-content: flex-end; align-items: center; gap: 8px; }
  .contacts svg { width: 12px; height: 12px; flex: none; }

  .pillars {
    position: absolute; right: 34px; top: 326px;
    color: var(--ink-light); font-size: 16px; font-weight: 700; letter-spacing: 0.3px;
    word-spacing: 5px; white-space: nowrap;
  }

  .card--back .brand {
    left: 0; right: 0; top: 130px; justify-content: center; font-size: 64px;
  }
  .card--back .brand__dot { width: 30px; height: 30px; }
  .tagline {
    position: absolute; left: 110px; right: 110px; top: 240px; text-align: center;
  }
  .tagline__rule { display: block; height: 1px; background: var(--cyan); }
  .tagline__text {
    display: block; color: var(--navy); font-size: 19px; padding: 8px 0;
  }
</style>
</head>
<body>
<main class="sheet">

  <section class="card card--front" aria-label="Business card front">
    <svg class="front-panels" width="700" height="400" viewBox="0 0 700 400" aria-hidden="true">
      <polygon points="322,0 700,0 700,290 356,290" fill="var(--navy)"/>
      <polygon points="356,290 700,290 700,400 370,400" fill="var(--green)"/>
    </svg>

    <div class="brand"><span class="brand__dot"></span>BrivoTerna</div>

    <div class="holder">
      <p class="holder__name">Teodoro Vinsquel</p>
      <p class="holder__role">CEO &amp; Founder</p>
    </div>

    <ul class="contacts">
      <li>+34 655.803.912
        <svg viewBox="0 0 12 12"><rect x="3" y="1" width="6" height="10" rx="1" fill="none" stroke="var(--cyan)" stroke-width="1.2"/></svg></li>
      <li>teodoro.vinsquel@brivoterna-example.com
        <svg viewBox="0 0 12 12"><rect x="1" y="3" width="10" height="7" fill="none" stroke="var(--cyan)" stroke-width="1.2"/><polyline points="1,3 6,7 11,3" fill="none" stroke="var(--cyan)" stroke-width="1.2"/></svg></li>
      <li>www.brivoterna-example.com
        <svg viewBox="0 0 12 12"><circle cx="6" cy="6" r="5" fill="none" stroke="var(--cyan)" stroke-width="1.2"/><ellipse cx="6" cy="6" rx="2.2" ry="5" fill="none" stroke="var(--cyan)" stroke-width="1"/><line x1="1" y1="6" x2="11" y2="6" stroke="var(--cyan)" stroke-width="1"/></svg></li>
    </ul>

    <p class="pillars">Strategy - Execution - Results</p>
  </section>

  <section class="card card--back" aria-label="Business card back">
    <div class="brand"><span class="brand__dot"></span>BrivoTerna</div>
    <div class="tagline">
      <span class="tagline__rule"></span>
      <span class="tagline__text">Lantern of the Steady Harvest</span>
      <span class="tagline__rule"></span>
    </div>
  </section>

</main>
</body>
</html>
```